Law Firm Business Card

This is a business card for a law firm that serves US military and veterans.

The card must have ONLY the following (we want an uncluttered look):

- Company logo (PNG, GIF, JPEG copies uploaded)
- A tagline reading: "a law firm for service members and veterans"
- My name and title: "Tobias Marlow" and "Attorney"
- My email: "tobias.marlow@brinmoorlegal.com"
- My number: "855-FIRM-ONE (347-6663)"

We are looking for a clean, simple layout with only the above information, likely printed on a bright white cotton stock. The font of our logo is DIN 1451, and the font used on our website is Helvetica Neue. The color of our logo is #336699, and we probably want the tagline in that color also, and my contact information in a dark grey. Please review our website at www.brinmoorlegal.com to ensure your card design complements our website style.

Thanks and we look forward to seeing your submissions.

A few notes:

- Two-sided submissions are ok
- Please don't add graphics (scales of justice, judges hammer, etc)

```html
<!DOCTYPE html>
<html lang="en">
<head>
<meta charset="utf-8">
<title>Brinmoor Legal – Business Card</title>
<link rel="stylesheet" href="https://fonts.googleapis.com/css2?family=Roboto+Condensed:wght@400;700&display=swap">
<style>
  :root {
    --brand-blue: #336699;
    --paper: #ffffff;
    --ink-light: #ffffff;
  }
  * { margin: 0; padding: 0; box-sizing: border-box; }
  html, body {
    width: 1200px;
    height: 720px;
    overflow: hidden;
    background: var(--paper);
  }
  .card {
    position: relative;
    width: 1200px;
    height: 720px;
    background: var(--paper);
    font-family: "Roboto Condensed", "Helvetica Neue", Arial, sans-serif;
  }
  .brand-side {
    position: absolute;
    left: 0; top: 0;
    width: 583px; height: 720px;
    display: flex;
    align-items: center;
    justify-content: center;
  }
  .brand-name {
    color: var(--brand-blue);
    font-weight: 700;
    font-size: 62px;
    letter-spacing: 1px;
    text-transform: uppercase;
    margin-top: -6px;
  }
  .divider-stripe {
    position: absolute;
    left: 583px; top: 0;
    width: 8px; height: 720px;
    background: var(--brand-blue);
  }
  .info-panel {
    position: absolute;
    left: 597px; top: 0;
    width: 603px; height: 720px;
    background: var(--brand-blue);
    color: var(--ink-light);
  }
  .person {
    position: absolute;
    left: 46px; top: 74px;
    font-weight: 700;
    font-size: 55px;
    line-height: 53px;
    text-transform: uppercase;
    letter-spacing: 0.3px;
  }
  .tagline {
    position: absolute;
    left: 46px; top: 254px;
    font-weight: 400;
    font-size: 24px;
    letter-spacing: 0.2px;
  }
  .contact {
    position: absolute;
    left: 40px;
    display: flex;
    align-items: center;
    gap: 16px;
    font-weight: 400;
    font-size: 27px;
  }
  .contact-email { top: 538px; }
  .contact-phone { top: 591px; }
  .contact-icon { flex: none; }
</style>
</head>
<body>
  <div class="card">
    <section class="brand-side">
      <div class="brand-name">Brinmoor Legal</div>
    </section>

    <div class="divider-stripe"></div>

    <section class="info-panel">
      <h1 class="person">Tobias Marlow<br>and<br>Attorney</h1>
      <p class="tagline">a law firm for service members and veteran</p>

      <div class="contact contact-email">
        <svg class="contact-icon" width="28" height="22" viewBox="0 0 28 22" aria-hidden="true">
          <rect x="1.5" y="1.5" width="25" height="19" fill="none" stroke="#fff" stroke-width="2.4"/>
          <path d="M1.5 1.5 L14 12 L26.5 1.5 M1.5 20.5 L11 10 M26.5 20.5 L17 10" fill="none" stroke="#fff" stroke-width="2.4"/>
        </svg>
        <span>tobias.marlow@brinmoorlegal.com</span>
      </div>

      <div class="contact contact-phone">
        <svg class="contact-icon" width="28" height="38" viewBox="0 0 28 38" aria-hidden="true">
          <rect x="4" y="1" width="20" height="36" rx="4" fill="#fff"/>
          <rect x="7" y="5" width="14" height="10" fill="#336699"/>
          <g fill="#336699">
            <rect x="7.5" y="19" width="3" height="3"/><rect x="12.5" y="19" width="3" height="3"/><rect x="17.5" y="19" width="3" height="3"/>
            <rect x="7.5" y="24" width="3" height="3"/><rect x="12.5" y="24" width="3" height="3"/><rect x="17.5" y="24" width="3" height="3"/>
            <rect x="7.5" y="29" width="3" height="3"/><rect x="12.5" y="29" width="3" height="3"/><rect x="17.5" y="29" width="3" height="3"/>
          </g>
        </svg>
        <span>855-FIRM-ONE (347-6663)</span>
      </div>
    </section>
  </div>
</body>
</html>
```